Design a New Business Card for Our Company

We are looking for fresh, unique, and a modern business card that reflects our roots as digital marketing agency focused on SEM.

Industry/Entity Type

Marketing

Contact Information for Business Card

looking for very unique out of the box designs. clean and modern that compliments our logo

Requirements
Must have
• colors should match our logo
• Front should have name, address, email, and phone/fax of the person, phone/fax are the same number
• back should have our url

```html
<!DOCTYPE html>
<html lang="en">
<head>
<meta charset="utf-8">
<title>Vantaro Digital – Business Card</title>
<link rel="stylesheet" href="https://fonts.googleapis.com/css2?family=Michroma&display=swap">
<style>
  :root {
    --bg: #e9e7e4;
    --brand-blue: #5b97d6;
    --brand-blue-deep: #4a86c7;
    --card-white: #ffffff;
    --card-grey: #dcdcdc;
    --ink: #2b2b2b;
    --ink-soft: #ffffffcc;
    --shadow: 0 14px 30px rgba(0, 0, 0, 0.18);
  }
  * { box-sizing: border-box; margin: 0; padding: 0; }
  html, body {
    width: 1200px;
    height: 878px;
    overflow: hidden;
    background: var(--bg);
    font-family: "Michroma", sans-serif;
  }
  .canvas {
    width: 1200px;
    height: 878px;
    display: flex;
    flex-direction: column;
    align-items: center;
    justify-content: center;
    gap: 40px;
  }
  .card {
    position: relative;
    width: 665px;
    height: 380px;
    border-radius: 4px;
    box-shadow: var(--shadow);
    overflow: hidden;
  }

  /* Back: brand + url */
  .card--back {
    background: linear-gradient(135deg, var(--brand-blue) 0%, var(--brand-blue-deep) 100%);
    color: var(--card-white);
  }
  .card--back .brand {
    position: absolute;
    left: 70px;
    top: 130px;
    display: flex;
    align-items: center;
    gap: 18px;
  }
  .brand__dot {
    width: 46px;
    height: 46px;
    border-radius: 50%;
    background: var(--card-white);
    flex: none;
  }
  .brand__name {
    font-size: 44px;
    letter-spacing: 1px;
    line-height: 1;
    text-transform: lowercase;
  }
  .card--back .url {
    position: absolute;
    left: 72px;
    top: 230px;
    font-size: 15px;
    letter-spacing: 9px;
    color: var(--ink-soft);
  }

  /* Front: personal details */
  .card--front {
    background: linear-gradient(160deg, var(--card-white) 0%, #f4f4f4 55%, var(--card-grey) 100%);
    color: var(--ink);
  }
  .details {
    position: absolute;
    left: 56px;
    top: 62px;
    font-size: 15px;
    line-height: 1.75;
  }
  .details__name {
    color: var(--brand-blue);
    font-size: 17px;
  }
  .details__title { margin-bottom: 6px; }
  .details__row span + span { margin-left: 28px; }
  .card--front .brand {
    position: absolute;
    right: 50px;
    top: 112px;
    display: flex;
    align-items: center;
    gap: 10px;
    color: var(--brand-blue);
  }
  .card--front .brand__dot {
    width: 24px;
    height: 24px;
    background: var(--brand-blue);
  }
  .card--front .brand__name { font-size: 24px; }
</style>
</head>
<body>
  <main class="canvas">
    <section class="card card--back" aria-label="Business card back">
      <div class="brand">
        <span class="brand__dot"></span>
        <span class="brand__name">vantaro digital</span>
      </div>
      <p class="url">www.webaddress.com</p>
    </section>

    <section class="card card--front" aria-label="Business card front">
      <div class="details">
        <p class="details__name">Your Name</p>
        <p class="details__title">Job Title</p>
        <p class="details__row"><span>P: 101 1010</span><span>F: 101 1010</span></p>
        <p class="details__row">E: services@vantaro</p>
        <p class="details__row">9 your adress, PO Box 101</p>
      </div>
      <div class="brand">
        <span class="brand__dot"></span>
        <span class="brand__name">vantaro</span>
      </div>
    </section>
  </main>
</body>
</html>
```